sydney wedding photography business needs a business card design

we need a business card design for a sydney based wedding photography and videography business. our business name is :golden hour studio and film. our target clients are 24-35 yrs female. our style is candid, organic, natural, dynamic. we are a team of young photographers and videographers, and help brides to create memories that they will cherish for the rest of their lives. the logo will be provided. we want an elegant design that reflects our style, and also want to give a great impression to our clients that we are one of the best studios in sydney and our brand means quality and premium service.

Target Market(s)

bride to be, 24-35 years old, living in sydney and surrunding areas

Industry/Entity Type

Wedding Photography

Contact Information for Business Card

address: 57 tarrant street, glenmore nsw 2047
mobile: 0431872259
phone: (02) 9163 2408
info@tidewillowstudio.net.au
www.tidewillowstudio.net.au
facebook:tidewillowweddings
instagram:tidewillowweddings

Font styles to use
Serif
Sans Serif

Requirements
Nice to have
• maybe add my slogan"memories beyond eternity" if the layout looks good
Should not have
• no black color, not good idea for wedding biz card

```html
<!DOCTYPE html>
<html lang="en">
<head>
<meta charset="utf-8">
<title>Golden Hour Studio and Film – Business Card</title>
<link rel="stylesheet" href="https://fonts.googleapis.com/css2?family=Cookie&family=PT+Sans:wght@400;700&display=swap">
<style>
  :root {
    --backdrop: #1a1a1a;
    --card-white: #ffffff;
    --gold: #e2b00c;
    --gold-light: #f4c500;
    --gold-deep: #cf9a12;
    --gold-ink: #a87a08;
    --text-dark: #3a3a3a;
  }
  * { margin: 0; padding: 0; box-sizing: border-box; }
  html, body {
    width: 1200px;
    height: 900px;
    overflow: hidden;
    background: var(--backdrop);
  }
  .stage { position: relative; width: 1200px; height: 900px; }

  .card {
    position: absolute;
    top: 170px;
    width: 347px;
    height: 561px;
    overflow: hidden;
  }

  /* Front */
  .card-front { left: 259px; background: var(--card-white); }
  .gold-tab {
    position: absolute;
    left: 102px;
    width: 143px;
    background: linear-gradient(180deg, var(--gold-deep), var(--gold-light));
  }
  .gold-tab.top { top: 0; height: 30px; }
  .gold-tab.bottom { bottom: 0; height: 28px; }

  .brand-mark {
    position: absolute;
    top: 92px;
    left: 0;
    width: 100%;
    text-align: center;
  }
  .brand-dot {
    display: block;
    margin: 0 auto;
    width: 96px;
    height: 96px;
    border-radius: 50%;
    background: linear-gradient(180deg, var(--gold-deep), var(--gold-light));
  }
  .brand-name {
    margin-top: 14px;
    font-family: "PT Sans", sans-serif;
    font-size: 14px;
    letter-spacing: 1px;
    color: var(--gold-deep);
    text-transform: lowercase;
  }

  .contact {
    position: absolute;
    top: 300px;
    left: 0;
    width: 100%;
    text-align: center;
    font-family: "PT Sans", sans-serif;
    color: var(--text-dark);
  }
  .person-name {
    font-family: "Cookie", cursive;
    font-size: 42px;
    line-height: 44px;
    font-weight: 400;
    color: var(--gold);
  }
  .person-role { font-size: 15px; margin-top: -2px; }
  .contact-lines { margin-top: 24px; font-size: 15px; line-height: 21px; }
  .address { margin-top: 16px; font-size: 15px; line-height: 17px; }

  /* Back */
  .card-back {
    left: 631px;
    background: radial-gradient(ellipse at 50% 45%, var(--gold-light) 0%, var(--gold) 45%, var(--gold-deep) 100%);
  }
  .back-name {
    position: absolute;
    left: 50%;
    top: 50%;
    transform: translate(-50%, -50%) rotate(-90deg);
    white-space: nowrap;
    font-family: "PT Sans", sans-serif;
    font-weight: 700;
    font-size: 30px;
    letter-spacing: 2px;
    color: var(--gold-ink);
    text-transform: lowercase;
  }
</style>
</head>
<body>
<main class="stage">
  <section class="card card-front">
    <div class="gold-tab top"></div>

    <div class="brand-mark">
      <span class="brand-dot"></span>
      <p class="brand-name">golden hour studio and film</p>
    </div>

    <div class="contact">
      <h1 class="person-name">Mia Harlow</h1>
      <p class="person-role">Managing Director</p>
      <p class="contact-lines">
        0431872259<br>
        info@tidewillowstudio.net.au<br>
        www.tidewillowstudio.net.au
      </p>
      <p class="address">
        57 tarrant street<br>
        glenmore nsw 2047
      </p>
    </div>

    <div class="gold-tab bottom"></div>
  </section>

  <section class="card card-back">
    <p class="back-name">golden hour studio and film</p>
  </section>
</main>
</body>
</html>
```